National Sales - Pick Up Truck Dealer

We need a logo design for a new vehicle dealership based in Sydney, Australia. The business name is Coastal Iron Haulers Motor Co. We will be selling American 'trucks/pick up trucks' like KRV, Torvan, Blaxer, Morrow T420, Kenzo Raptors, Morrow T640 and the likes.

These vehicles are a luxury option and we would like the logo to be strong, luxurious and masculine.Colours will be black and red or black and blue with the option of grey and white.

Target Market(s)

Men

Industry/Entity Type

Car Dealer

Contact Information for Business Card

Dennis Harlowe
Managing Director
0412 639 274
den@qelvtrk.com.au

Level 5, Brindle Parkway
17 Pemberly Lane
Baulkham Hills
NSW
Australia
Licence No: MD493152

Back of the card

qelvtrk.com.au

Font styles to use
Sans Serif

Colors

Designer to choose colors to be used in the design.

Requirements
Must have
• The company logo that is in the attachments, you can choose from the three which one you would like to work with. Must have vehicle images ....Please look at the attachments as they show examples of what we like and also provides potential images. If you choose to put an image on the front even if it is just the front of the vehicle can you please use the Black KRV Sorrento. Must have all details from the business card details section front and back
Nice to have
• N/A
Should not have
• No cars or standard trucks, please refer to the attached images to understand the product . Should not have any new logos or branding. No other colours besides what is in the logo you choose.

```html
<!DOCTYPE html>
<html lang="en">
<head>
<meta charset="utf-8">
<title>Coastal Iron Haulers Motor Co – Business Card</title>
<link href="https://fonts.googleapis.com/css2?family=Open+Sans:wght@400;600&family=Oswald:wght@600&display=swap" rel="stylesheet">
<style>
  :root {
    --backdrop: #2b2b2c;
    --card: #1f1f20;
    --text: #e9e9e9;
    --muted: #cfcfcf;
    --accent: #1c7fd0;
    --logo: #b9bcc0;
  }
  * { margin: 0; padding: 0; box-sizing: border-box; }
  html, body {
    width: 1200px; height: 900px; overflow: hidden;
    background: var(--backdrop);
    font-family: "Open Sans", sans-serif;
    color: var(--text);
  }
  .card {
    position: absolute;
    left: 280px;
    width: 640px; height: 390px;
    background: var(--card);
    box-shadow: 0 10px 30px rgba(0,0,0,0.45);
  }
  .card-front { top: 30px; }
  .card-back  { top: 480px; }

  .brand {
    position: absolute;
    left: 0; right: 0; top: 130px;
    text-align: center;
    font-weight: 600;
    font-size: 30px;
    letter-spacing: 1px;
    color: var(--logo);
    text-transform: uppercase;
    line-height: 1.3;
  }
  .front-url {
    position: absolute;
    left: 0; right: 0; bottom: 44px;
    text-align: center;
    font-size: 15px;
    letter-spacing: 1.5px;
    color: var(--muted);
  }
  .url-key { color: var(--accent); }

  .licence {
    position: absolute;
    top: 34px; right: 36px;
    font-size: 15px;
    letter-spacing: 0.5px;
    color: var(--muted);
  }
  .person {
    position: absolute;
    top: 128px; right: 340px;
    text-align: right;
  }
  .person-name {
    font-family: "Oswald", sans-serif;
    font-weight: 600;
    font-size: 42px;
    line-height: 1.05;
    text-transform: uppercase;
    color: #ffffff;
  }
  .person-role {
    font-weight: 600;
    font-size: 17px;
    color: #ffffff;
  }
  .divider {
    position: absolute;
    left: 318px; top: 132px;
    width: 2px; height: 88px;
    background: var(--text);
  }
  .contacts {
    position: absolute;
    left: 336px; top: 140px;
    list-style: none;
    font-size: 17px;
    letter-spacing: 0.5px;
    color: var(--text);
  }
  .contacts li {
    display: flex; align-items: center;
    height: 26px;
  }
  .contacts svg { width: 16px; height: 16px; margin-right: 14px; flex: none; }
  .address {
    position: absolute;
    left: 44px; bottom: 44px;
    font-size: 16px;
    color: var(--muted);
  }
</style>
</head>
<body>

<section class="card card-front">
  <div class="brand">Coastal Iron Haulers<br>Motor Co</div>
  <p class="front-url">www.<span class="url-key">qelvtrk</span>.com.au</p>
</section>

<section class="card card-back">
  <p class="licence">Licence No: MD493152</p>

  <div class="person">
    <h1 class="person-name">Dennis Harlowe</h1>
    <p class="person-role">Managing Director</p>
  </div>

  <div class="divider"></div>

  <ul class="contacts">
    <li>
      <svg viewBox="0 0 16 16" aria-hidden="true"><rect x="4" y="1" width="8" height="14" rx="1.5" fill="none" stroke="var(--accent)" stroke-width="1.6"/><circle cx="8" cy="12.3" r="0.9" fill="var(--accent)"/></svg>
      0412 639 274
    </li>
    <li>
      <svg viewBox="0 0 16 16" aria-hidden="true"><rect x="1" y="3" width="14" height="10" rx="1" fill="none" stroke="var(--accent)" stroke-width="1.6"/><path d="M1.5 3.8 8 9l6.5-5.2" fill="none" stroke="var(--accent)" stroke-width="1.6"/></svg>
      den@qelvtrk.com.au
    </li>
    <li>
      <svg viewBox="0 0 16 16" aria-hidden="true"><circle cx="8" cy="8" r="6.5" fill="none" stroke="var(--accent)" stroke-width="1.6"/><path d="M1.5 8h13M8 1.5c-3 3.5-3 9.5 0 13M8 1.5c3 3.5 3 9.5 0 13" fill="none" stroke="var(--accent)" stroke-width="1.2"/></svg>
      www.<span class="url-key">qelvtrk</span>.com.au
    </li>
  </ul>

  <p class="address">Level 5, Brindle Parkway, 17 Pemberly Lane,Baulkham Hills,NSW, Australia</p>
</section>

</body>
</html>
```